Animal Horse & Bedding Company Needs a Website Coded & Designed

We need a website for a new animal bedding and feed company that is visually grabbing and vibrant. We would like to see a website that displays trust, quality and confidence. Needs to be responsive and mobile friendly for all browsers and coded for both Android & IOS. SEO is also important.

Joomla or Wordpress – must be both desktop and mobile friendly with fast page load speed. Need the ability to edit ourselves in Wordpress or Joomla.

Full details attached below with some layout and content ideas.

Coding

Coded - Design and coding required

Number of Pages Required

5+ page

Font styles to use
Sans Serif

Requirements
Must have
• Needs to be responsive and mobile friendly for all browsers and coded for both Android & IOS. SEO is also important.

Wordpress – must be both desktop and mobile friendly with fast page load speed. Need the ability to edit ourselves in Wordpress.

Logo Colours:
Dark Brown
CMYK: 50 / 70 / 80 / 70
Pantone: 4625C

Orange
CMYK: 0 / 50 / 100 / 0
Pantone: 144C
Nice to have
• Use picture of building attached and super impose logo on building.

```html
<!DOCTYPE html>
<html lang="en">
<head>
<meta charset="utf-8">
<title>Meadowline Bedding &amp; Feed</title>
<link href="https://fonts.googleapis.com/css2?family=Bebas+Neue&family=Poppins:wght@400;500;600&display=swap" rel="stylesheet">
<style>
:root{
  --brown:#3b2416;
  --brown-text:#3a2214;
  --orange:#f7941d;
  --cream:#fdf8f1;
  --white:#ffffff;
  --ink:#2b2b2b;
}
*{box-sizing:border-box;margin:0;padding:0}
html,body{width:1200px;height:2634px;overflow:hidden;background:var(--white)}
body{font-family:"Poppins",sans-serif;color:var(--ink);position:relative}
.page{position:absolute;left:72px;top:102px;width:1056px;height:2438px;background:var(--white);overflow:hidden}
.abs{position:absolute}
.display{font-family:"Bebas Neue",sans-serif;font-weight:400;letter-spacing:1px}

/* header */
.topbar{left:0;top:0;width:1056px;height:88px;background:var(--brown)}
.contact{left:68px;color:#fff;font-size:10.5px;display:flex;align-items:center;gap:18px}
.contact svg{width:14px;height:14px}
.brand-tab{left:450px;top:0;width:160px;height:88px}
.brand-name{left:450px;top:46px;width:160px;text-align:center;color:var(--brown-text);font-size:24px}
.search{left:763px;top:31px;width:237px;height:27px;background:#fff;border-radius:3px;font-size:10px;color:#b9b9b9;padding:6px 14px}
.search svg{position:absolute;right:12px;top:8px;width:11px;height:11px}
.nav{left:0;top:88px;width:1056px;height:31px;background:var(--orange);display:flex;justify-content:center;gap:50px;align-items:center;font-size:13.5px;color:#fff;padding-right:40px}

/* hero */
.hero{left:0;top:119px;width:1056px;height:520px;background:linear-gradient(100deg,#d9a24b 0%,#e7c46a 30%,#c99a55 55%,#8a4a1c 75%,#b3c65a 100%)}
.hero-grass{left:0;top:540px;width:1056px;height:100px;background:linear-gradient(180deg,rgba(176,196,70,0) 0%,#9fbd3f 55%,#ffffff 100%)}
.hero-kicker{left:84px;top:233px;color:#fff;font-size:34px}
.hero-title{left:82px;top:262px;color:#fff;font-size:96px;line-height:1}
.hero-sub{left:84px;top:372px;color:#fff;font-size:52px;line-height:1}
.btn{background:var(--orange);color:#fff;font-family:"Bebas Neue",sans-serif;font-size:17px;letter-spacing:1.5px;text-align:center;line-height:31px;height:31px;width:117px;border-radius:2px;box-shadow:0 3px 4px rgba(0,0,0,.18)}

/* sections */
.heading{font-size:44px;color:var(--brown-text);line-height:1}
.rule{height:4px;width:69px;background:var(--brown-text)}
.body-copy{font-size:12.2px;line-height:18.4px;color:#333}
.list{font-size:11.4px;line-height:17.6px;letter-spacing:.5px;color:#2f2f2f;list-style:none}
.list li::before{content:"• "}
.mark{left:120px;top:740px;width:260px;height:260px;display:flex;align-items:center;justify-content:center;gap:10px;color:var(--brown-text);font-size:40px}
.mark span.dot{width:22px;height:22px;border-radius:50%;background:var(--orange)}
.band{left:0;top:1082px;width:1056px;height:432px;background:var(--cream)}
.photo-foal{left:513px;top:1120px;width:440px;height:349px;background:linear-gradient(180deg,#a8b0a8 0%,#7ea650 45%,#5fa52e 100%)}
.photo-grazing{left:88px;top:1580px;width:426px;height:378px;background:linear-gradient(180deg,#8fa85a 0%,#7a9640 40%,#6a4128 55%,#7fb247 80%)}

/* newsletter & footer */
.footer{left:0;top:2125px;width:1056px;height:313px;background:var(--brown)}
.newsletter{left:121px;top:2071px;width:813px;height:80px;background:var(--orange)}
.nl-title{left:30px;top:26px;font-size:25px;color:var(--brown-text)}
.nl-input{left:279px;top:23px;width:359px;height:33px;background:#fff;font-size:12px;color:#9a9a9a;padding:9px 15px}
.nl-btn{left:651px;top:23px;width:143px;height:33px;background:var(--brown);color:#fff;font-size:20px;text-align:center;line-height:34px}
.f-brand{left:146px;top:2200px;color:#fff;font-size:28px;display:flex;align-items:center;gap:8px}
.f-brand .dot{width:14px;height:14px;border-radius:50%;background:var(--orange)}
.f-about{left:143px;top:2286px;width:200px;color:#fff;font-size:11.6px;line-height:16.3px;letter-spacing:.6px}
.f-head{color:#fff;font-size:18.5px;font-weight:500;padding-bottom:4px;border-bottom:2px solid #fff;display:inline-block;line-height:1.2}
.f-phones{font-size:12px;color:#fff;font-weight:500;letter-spacing:.5px;line-height:39px}
.f-links{font-size:11.5px;color:#fff;font-weight:500;letter-spacing:.5px;line-height:18.8px;list-style:none}
.f-social{list-style:none;font-size:11px;color:#fff;letter-spacing:.5px;line-height:25.5px}
.f-social li{display:flex;align-items:center;gap:17px}
.f-social .ico{width:13px;height:13px;border:1.5px solid #fff;border-radius:3px}
.f-rule{left:121px;top:2388px;width:813px;height:1px;background:#8a7466}
.copyright{left:0;top:2402px;width:1056px;text-align:center;color:#fff;font-size:11.5px}
</style>
</head>
<body>
<div class="page">

  <header>
    <div class="abs topbar"></div>
    <div class="abs contact" style="top:27px">
      <svg viewBox="0 0 16 16" aria-hidden="true"><path d="M3 1l3 3-2 2c1 2 3 4 5 5l2-2 3 3-2 3C7 14 2 9 1 3z" fill="#f7941d"/></svg>
      <span>0800-000-1234</span>
    </div>
    <div class="abs contact" style="top:48px">
      <svg viewBox="0 0 16 16" aria-hidden="true"><rect x="1" y="3" width="14" height="10" fill="#f7941d"/><path d="M1 3l7 6 7-6" stroke="#3b2416" stroke-width="1.4" fill="none"/></svg>
      <span>hello@meadowline.example</span>
    </div>
    <svg class="abs brand-tab" viewBox="0 0 160 88" aria-hidden="true"><path d="M0 88 L28 46 L80 0 L132 46 L160 88Z" fill="#fff"/></svg>
    <div class="abs brand-name display">Meadowline</div>
    <div class="abs search">Search
      <svg viewBox="0 0 12 12" aria-hidden="true"><circle cx="5" cy="5" r="3.6" stroke="#f7941d" stroke-width="1.6" fill="none"/><path d="M7.6 7.6L11 11" stroke="#f7941d" stroke-width="1.8"/></svg>
    </div>
    <nav class="abs nav">
      <span>Home</span><span>About</span><span>Feed</span><span>Bedding</span><span>Contact Us</span><span>Requets Quote</span>
    </nav>
  </header>

  <section>
    <div class="abs hero" role="img" aria-label="Chestnut horse with a flowing blond mane standing in a golden meadow at sunset"></div>
    <div class="abs hero-grass" aria-hidden="true"></div>
    <div class="abs hero-kicker display">Wellcome</div>
    <h1 class="abs hero-title display">Meadowline</h1>
    <div class="abs hero-sub display">Bedding &amp; Feed</div>
    <div class="abs btn" style="left:84px;top:443px">Shop Now</div>
  </section>

  <section>
    <div class="abs mark display"><span class="dot"></span>Meadowline</div>
    <h2 class="abs heading display" style="left:506px;top:725px">About Us</h2>
    <div class="abs rule" style="left:506px;top:768px"></div>
    <p class="abs body-copy" style="left:506px;top:797px;width:410px">Looking for the best bedding and feed for your horse, livestock or household pet look no further.&nbsp; We use premium locally sourced straw and hay in all of our products and are committed in providing quality products and service.<br>Your animal deserves the very best in health and comfort to keep them healthy, strong and happy.&nbsp; Our products are designed for horses, livestock (goats, cattle and sheep), small caged animals (rabbits, guinea pigs and more).</p>
    <div class="abs btn" style="left:506px;top:969px">Learn More</div>
  </section>

  <section>
    <div class="abs band"></div>
    <h2 class="abs heading display" style="left:92px;top:1154px">Bedding Benefit</h2>
    <div class="abs rule" style="left:92px;top:1198px"></div>
    <ul class="abs list" style="left:92px;top:1234px">
      <li>100% Natural Chopped Straw</li>
      <li>Low Dust</li>
      <li>Chemical &amp; Additive Free</li>
      <li>Clean &amp; Highly Absorbent</li>
      <li>Cheaper than Wood Shavings</li>
      <li>Economic – less used and less wasted</li>
      <li>Environmentally Friendly – Recyclable &amp; Compostable</li>
    </ul>
    <div class="abs btn" style="left:92px;top:1393px">Shop Now</div>
    <div class="abs photo-foal" role="img" aria-label="Young brown foal carrying a feed bucket on green grass"></div>
  </section>

  <section>
    <div class="abs photo-grazing" role="img" aria-label="Bay horse grazing in a green pasture beside trees"></div>
    <h2 class="abs heading display" style="left:576px;top:1630px">Feed Benefit</h2>
    <div class="abs rule" style="left:576px;top:1674px"></div>
    <ul class="abs list" style="left:576px;top:1710px">
      <li>100% Natural</li>
      <li>Chemical &amp; Additive Free</li>
      <li>Available in Pellets or Cubes</li>
      <li>High Protein Content</li>
      <li>Eliminate Waste In Feeding</li>
      <li>Clean - Eliminates Dust From Feeding Baled Hay</li>
      <li>Cost Effective</li>
      <li>Convenient</li>
      <li>Less wasted feed</li>
    </ul>
    <div class="abs btn" style="left:576px;top:1892px">Shop Now</div>
  </section>

  <footer>
    <div class="abs footer"></div>
    <div class="abs newsletter">
      <div class="abs nl-title display">Subscribe for Newsletter</div>
      <div class="abs nl-input">Your Email Address</div>
      <div class="abs nl-btn display">Subscribe</div>
    </div>
    <div class="abs f-brand display"><span class="dot"></span>Meadowline</div>
    <p class="abs f-about">Meadowline offers supply and delivery of fresh bedding as well as removal of waste bedding.</p>

    <div class="abs" style="left:408px;top:2198px">
      <div class="f-head">Get in touch</div>
      <div class="f-phones" style="margin-top:10px">0811-000-1100<br>022-0000-1122<br>0811-000-2200</div>
    </div>
    <div class="abs" style="left:595px;top:2198px">
      <div class="f-head">Useful Links</div>
      <ul class="f-links" style="margin-top:16px">
        <li>Home</li><li>About</li><li>Feed</li><li>Bedding</li><li>Contact Us</li><li>Request Quote</li>
      </ul>
    </div>
    <div class="abs" style="left:781px;top:2198px">
      <div class="f-head">Connect</div>
      <ul class="f-social" style="margin-top:11px">
        <li><span class="ico"></span>Photos</li>
        <li><span class="ico"></span>Community</li>
        <li><span class="ico"></span>Updates</li>
        <li><span class="ico"></span>Videos</li>
      </ul>
    </div>
    <div class="abs f-rule"></div>
    <div class="abs copyright">© Copyright 2020 Meadowline. All Rights Reserved.</div>
  </footer>

</div>
</body>
</html>
```